Zimbal, a future commerce website

Zimbal will be a commerce website; the project is quite large, and for now I just require three pages and the main bar to be crafted; If chosen your design, I will require you to work with me in a freelance job for the rest of the site to be made.
The following is one way to put Zimbal’s building blocks; you can propose another.
A list of webpages, whose design I like, is in the first document.
-Design specification
Zimbal’s interface should be minimal and intuitive.
Its design should make the user perceive Zimbal as innovative; I will incline for an out of the box design.
--Main bar
It will contain the site logo, a search bar, and four buttons, listed below.
---Notifications button
It will display a sidebar with containers; each container will have an icon, the notification, and one or two buttons; two example notifications and its respective buttons are in the second document.
It shall stand out when there are unseen notifications.
---Shopping cart button
A sidebar will be toggled on click with added product previews.
---Sell Button
---Account button
When clicked it will display a pane whose elements will depend on the user
status.
----If logged
It will display seller’s store image, a button linking to the main section of the account section, a button linking to in-process bought items of the account section, and a button linking to in-process sold items of the account section.
----If not logged
It will contain the elements for the user to either log in or register; for the former, email or username and password will be asked, for the latter, username, email, and password, this last one being asked twice.
--Product previews
Each, will have a title, a product image, and the product’s most important characteristics; most characteristics will have alongside an icon, which will display on mouse over the characteristic name, or, a name. Characteristics of two product categories whose product previews will contain an icon alongside are in the third document.
--Main page
Product previews of several categories will be displayed here; in order to reflect recommendation, some should have distinct size.
A list of categories will be present in this page; it may be toggled by a button contained in the main bar, or be displayed permanently.
A text conveying the message that all purchases made with Zimbal payment system are protected will be contained in a full width element which will be positioned below the main bar of this page; a “Learn more” link will be positioned in this element.
--Product page creation page
It will be displayed as part of the publication page.
It will be a "what you see is what you get" design system; the user will choose from several templates and fill the appropriate spaces; where text must be put, sample text will be present, and, where an image must, a plus sign and a “Add image” text will be present; submit please two templates; for the user to be able to add more content, at the bottom of the template there will be four layouts, upon click of one, it will be added.
Regarding the shipping menu, there will always be an empty box with a plus sign and a “Add shipping option” text, if clicked the user will be able to either fill it with company name, shipping time, and price, or to put the text “Arrange with seller” in it (if there is no other box with that text).
--Product page
It will not occupy the whole viewport; there will be vertical holes at the leftmost and rightmost parts of the viewport.
It will contain: price (which should include shipping in type one publications), sale price (for some product pages), countdown of sale price, average seller’s handling time, seller’s reputation indicator as measured by percentage of positive reviews received, seller’s store/profile image, seller’s username, a shipping menu consisting of boxes (selected will be displayed differently), “Buy” and “Add to cart” buttons, a section to view and ask questions, and seller provided images and text.
Previews of similar products will also be present.
Reason: Designs still require some work

```html
<!DOCTYPE html>
<html lang="en">
<head>
<meta charset="utf-8">
<title>Zimbal — Store</title>
<link href="https://fonts.googleapis.com/css2?family=Roboto:wght@400;500;700;900&display=swap" rel="stylesheet">
<style>
:root{
  --navy:#0d3a66;
  --navy-deep:#0a2f55;
  --hero-a:#4cc6e4;
  --hero-b:#9fe0f0;
  --pink:#e43a8e;
  --orange:#f26b21;
  --ink:#2b2f36;
  --muted:#8a9099;
  --line:#e3e6ea;
  --soft:#f4f6f8;
  --white:#ffffff;
  --blue:#1a7fc4;
  --icon:#7d8794;
}
*{box-sizing:border-box;margin:0;padding:0}
html,body{width:1200px;height:2604px;overflow:hidden}
body{font-family:"Roboto",Arial,sans-serif;color:var(--ink);background:var(--white);position:relative}
.abs{position:absolute}

/* main bar */
.topbar{left:0;top:0;width:1200px;height:62px;display:flex;align-items:center;padding:0 60px;z-index:3;background:rgba(10,47,85,.22)}
.brand{color:var(--white);font-weight:900;font-size:24px;letter-spacing:1px}
.nav{display:flex;gap:28px;margin-left:auto;margin-right:30px}
.nav a{color:var(--white);font-size:12px;font-weight:700;text-decoration:none;letter-spacing:.5px}
.search{width:96px;height:24px;border:1px solid rgba(255,255,255,.75);border-radius:3px;color:var(--white);font-size:11px;display:flex;align-items:center;padding-left:8px;gap:6px}
.icon-btn{margin-left:24px;position:relative;display:flex;align-items:center}
.badge{position:absolute;top:-6px;right:-9px;background:var(--orange);color:#fff;font-size:9px;font-weight:700;width:16px;height:16px;border-radius:50%;display:flex;align-items:center;justify-content:center;border:1.5px solid #fff}
.sell{margin-left:24px;height:26px;padding:0 14px;border-radius:3px}
.account{margin-left:24px;color:var(--white);font-size:12px;font-weight:700;display:flex;align-items:center;gap:8px}

/* protection strip */
.protect{left:0;top:62px;width:1200px;height:36px;z-index:2;background:var(--navy);color:#dbe6f2;font-size:12px;display:flex;align-items:center;justify-content:center;gap:10px}
.protect a{color:var(--white);font-weight:700;text-decoration:underline;margin-left:6px}

/* hero */
.hero{left:0;top:0;width:1200px;height:640px;background:linear-gradient(100deg,var(--hero-a),var(--hero-b) 60%,#c7ecf5)}
.hero-photo{left:360px;top:0;width:840px;height:640px;background:radial-gradient(ellipse 42% 48% at 52% 38%,#f05aa6 0,var(--pink) 45%,rgba(228,58,142,0) 100%)}
.hero-title{left:155px;top:288px;color:var(--white);font-weight:900;font-size:40px;line-height:1.1}
.hero-title small{display:block;font-size:30px;font-weight:900}
.hero-title small b{font-size:46px}
.btn{background:var(--orange);color:var(--white);font-size:12px;font-weight:700;letter-spacing:.5px;display:inline-flex;align-items:center;justify-content:center;border-radius:2px}
.hero-btn{left:155px;top:432px;width:118px;height:36px}
.dots{left:160px;top:596px;display:flex;gap:10px}
.dots i{width:12px;height:12px;border-radius:50%;background:rgba(255,255,255,.65)}
.dots i:first-child{background:transparent;border:2px solid #fff}

/* sidebar */
.side-title,.section-title{font-size:14px;font-weight:900;color:var(--navy);letter-spacing:.5px}
.cats{left:60px;top:702px;width:220px}
.cat-list{margin-top:18px;border:1px solid var(--line)}
.cat-list li{list-style:none;height:32px;display:flex;align-items:center;padding-left:20px;font-size:12px;color:#555;border-bottom:1px solid var(--line)}
.cat-list li:last-child{border-bottom:none}
.cat-list li.active{background:#e9edf2;font-weight:700;color:var(--ink)}
.brands{left:60px;top:1414px;width:220px}
.brand-list{margin-top:16px;border:1px solid var(--line)}
.brand-list li{list-style:none;height:34px;display:flex;align-items:center;justify-content:space-between;padding:0 16px 0 20px;font-size:12px;color:#555;border-bottom:1px solid var(--line)}
.brand-list li:last-child{border-bottom:none}
.check{width:13px;height:13px;border:1px solid #b8bec6;border-radius:2px}

/* products */
.products{left:304px;top:702px;width:856px}
.grid{margin-top:22px;display:grid;grid-template-columns:repeat(4,205px);gap:24px 12px}
.card{height:340px;border:1px solid var(--line);background:var(--white);display:flex;flex-direction:column;align-items:center;padding:16px 14px;text-align:center}
.card .pic{width:170px;height:160px;border-radius:4px;flex:none}
.card h3{margin-top:14px;font-size:12px;font-weight:700;color:var(--ink);letter-spacing:.4px}
.card p{margin-top:7px;font-size:10px;line-height:1.45;color:var(--muted)}
.specs{margin-top:9px;display:flex;gap:14px;justify-content:center}
.spec{width:22px;height:22px;border-radius:50%;background:var(--soft);display:flex;align-items:center;justify-content:center}
.spec svg{width:12px;height:12px}
.price{margin-top:9px;font-size:14px;font-weight:700;color:var(--orange)}
.promo{background:var(--navy);border-color:var(--navy);align-items:flex-start;text-align:left;padding:28px 22px}
.promo p{color:#dbe6f2;font-size:11px;line-height:1.6;margin:0}
.promo .btn{margin-top:30px;width:92px;height:30px;font-size:10px}

.more{left:714px;top:1860px;width:40px;height:40px;border:1px solid #cfd4da;border-radius:50%;display:flex;align-items:center;justify-content:center;background:#fff}

/* offers */
.offers{left:304px;top:1928px;width:856px;display:grid;grid-template-columns:repeat(3,1fr);gap:14px}
.offer{height:232px;background:#eef1f4;position:relative;overflow:hidden;padding:26px 20px}
.offer.alt{background:#dfe8f1}
.offer h4{font-size:13px;font-weight:900;color:var(--blue);line-height:1.25;width:120px}
.offer p{margin-top:10px;font-size:10px;line-height:1.5;color:var(--muted);width:118px}
.offer .btn{position:absolute;left:20px;top:172px;width:84px;height:28px;font-size:10px;background:var(--navy)}
.offer .pic{position:absolute;right:14px;top:22px;width:120px;height:190px;border-radius:4px}

/* footer */
.footer{left:0;top:2208px;width:1200px;height:396px;background:var(--navy);color:#c9d6e6}
.fcol{position:absolute;top:52px}
.fcol h5{font-size:13px;font-weight:900;color:var(--white);letter-spacing:.5px;margin-bottom:16px}
.fcol p{font-size:11px;line-height:1.6}
.fcol ul li{list-style:none;font-size:11px;line-height:22px}
.field{margin-top:22px;width:260px;height:40px;border:1px solid #4e6f93;display:flex;align-items:center;padding-left:14px;font-size:11px;color:#9fb2c8;gap:8px}
.subscribe{margin-top:14px;width:200px;height:40px}
.social li{display:flex;align-items:center;gap:12px}
.social i{width:14px;height:14px;border-radius:50%;background:#4e6f93;display:inline-block}
.contact li{display:flex;gap:12px;align-items:flex-start}
.fbar{position:absolute;left:60px;right:60px;top:340px;border-top:1px solid #22517f;padding-top:16px;font-size:10px;color:#9fb2c8;text-align:right}
</style>
</head>
<body>

<svg width="0" height="0" style="position:absolute">
  <defs>
    <symbol id="i-ship" viewBox="0 0 12 12"><path d="M0 3h7v5H0zM7 5h3l2 2v1H7z" fill="#7d8794"/><circle cx="2.5" cy="9.5" r="1.3" fill="#7d8794"/><circle cx="9.5" cy="9.5" r="1.3" fill="#7d8794"/></symbol>
    <symbol id="i-safe" viewBox="0 0 12 12"><path d="M6 0l5 2v4c0 3-2.5 5-5 6-2.5-1-5-3-5-6V2z" fill="#7d8794"/><path d="M3.5 6l2 2 3-3.5" fill="none" stroke="#fff" stroke-width="1.3"/></symbol>
    <symbol id="i-star" viewBox="0 0 12 12"><path d="M6 .5l1.7 3.6 3.8.4-2.9 2.6.9 3.9L6 9 2.5 11l.9-3.9L.5 4.5l3.8-.4z" fill="#7d8794"/></symbol>
  </defs>
</svg>

<div class="abs hero"></div>
<div class="abs hero-photo" role="img" aria-label="Woman in sunglasses and hat holding a pink umbrella"></div>

<header class="abs topbar">
  <div class="brand">ZIMBAL</div>
  <nav class="nav"><a>HOME</a><a>PRODUCTS</a><a>SERVICES</a><a>CONTACT</a></nav>
  <div class="search">
    <svg width="10" height="10" viewBox="0 0 10 10"><circle cx="4" cy="4" r="3" fill="none" stroke="#fff" stroke-width="1.3"/><line x1="6.3" y1="6.3" x2="9" y2="9" stroke="#fff" stroke-width="1.3"/></svg>Search
  </div>
  <div class="icon-btn" aria-label="Notifications">
    <svg width="18" height="20" viewBox="0 0 18 20"><path d="M9 1a6 6 0 0 1 6 6v5l2 3H1l2-3V7a6 6 0 0 1 6-6z" fill="#fff"/><path d="M6.5 17a2.5 2.5 0 0 0 5 0z" fill="#fff"/></svg>
    <span class="badge">3</span>
  </div>
  <div class="icon-btn" aria-label="Shopping cart">
    <svg width="24" height="20" viewBox="0 0 24 20"><path d="M1 2h4l3 11h12l3-8H7" fill="none" stroke="#fff" stroke-width="2"/><circle cx="9" cy="17" r="1.8" fill="#fff"/><circle cx="19" cy="17" r="1.8" fill="#fff"/></svg>
    <span class="badge">2</span>
  </div>
  <div class="btn sell">SELL</div>
  <div class="account">
    <svg width="12" height="12" viewBox="0 0 12 12"><circle cx="6" cy="3.5" r="2.8" fill="#fff"/><path d="M0.5 12c0-3.2 2.5-5 5.5-5s5.5 1.8 5.5 5z" fill="#fff"/></svg>MY ACCOUNT
  </div>
</header>

<div class="abs protect">
  <svg width="14" height="14" viewBox="0 0 12 12"><path d="M6 0l5 2v4c0 3-2.5 5-5 6-2.5-1-5-3-5-6V2z" fill="#f26b21"/><path d="M3.5 6l2 2 3-3.5" fill="none" stroke="#fff" stroke-width="1.3"/></svg>
  Every purchase made with Zimbal Pay is fully protected.<a>Learn more</a>
</div>

<div class="abs hero-title">WOMEN CLOTHING<small>UPTO <b>10%</b></small></div>
<div class="abs btn hero-btn">SHOP NOW</div>
<div class="abs dots"><i></i><i></i><i></i><i></i></div>

<aside class="abs cats">
  <div class="side-title">CATEGORIES</div>
  <ul class="cat-list">
    <li class="active">All</li><li>Women</li><li>Men</li><li>Baby &amp; Kids</li><li>Home &amp; Furniture</li>
    <li>Book &amp; Media</li><li>Mobiles</li><li>Tablets</li><li>Travel</li><li>Electronics</li>
    <li>Headphones</li><li>LED TV</li><li>Sports</li><li>Camera</li><li>Clothing</li>
    <li>Toys</li><li>Furniture</li>
  </ul>
</aside>

<aside class="abs brands">
  <div class="side-title">BRAND</div>
  <ul class="brand-list">
    <li>Orchard<span class="check"></span></li><li>Sonex<span class="check"></span></li>
    <li>Samvel<span class="check"></span></li><li>Norvik<span class="check"></span></li>
    <li>Macrosys<span class="check"></span></li><li>Minimax<span class="check"></span></li>
  </ul>
</aside>

<section class="abs products">
  <div class="section-title">PRODUCTS</div>
  <div class="grid">
    <div class="card promo">
      <p>Contrary to popular belief, good things come to those who shop here. Fresh picks arrive every week, with fair prices, quick delivery and care in every parcel we send out to you.</p>
      <span class="btn">READ MORE</span>
    </div>
    <div class="card"><div class="pic" role="img" aria-label="Orange leather handbag" style="background:linear-gradient(#f6efe8,#e8a064)"></div><h3>BAG</h3><p>Soft leather bag with roomy inside, made to last for years.</p><div class="specs"><span class="spec" title="Free shipping"><svg><use href="#i-ship"/></svg></span><span class="spec" title="Protected purchase"><svg><use href="#i-safe"/></svg></span><span class="spec" title="Top rated"><svg><use href="#i-star"/></svg></span></div><div class="price">$25.00</div></div>
    <div class="card"><div class="pic" role="img" aria-label="Denim shirt and shorts outfit" style="background:linear-gradient(#f1f3f6,#8ea7c4)"></div><h3>DRESSES</h3><p>Light summer outfit in washed denim, easy to wear all day.</p><div class="specs"><span class="spec" title="Free shipping"><svg><use href="#i-ship"/></svg></span><span class="spec" title="Protected purchase"><svg><use href="#i-safe"/></svg></span><span class="spec" title="Top rated"><svg><use href="#i-star"/></svg></span></div><div class="price">$25.00</div></div>
    <div class="card"><div class="pic" role="img" aria-label="Pair of red high heel shoes" style="background:linear-gradient(#f7eeee,#d8343d)"></div><h3>SHOE</h3><p>Glossy red heels that bring a bold touch to any evening.</p><div class="specs"><span class="spec" title="Free shipping"><svg><use href="#i-ship"/></svg></span><span class="spec" title="Protected purchase"><svg><use href="#i-safe"/></svg></span><span class="spec" title="Top rated"><svg><use href="#i-star"/></svg></span></div><div class="price">$25.00</div></div>

    <div class="card"><div class="pic" role="img" aria-label="Glass perfume bottle" style="background:linear-gradient(#f7f3f1,#e5c7bf)"></div><h3>PERFUME</h3><p>Fresh floral scent in a clear glass bottle with silver cap.</p><div class="specs"><span class="spec" title="Free shipping"><svg><use href="#i-ship"/></svg></span><span class="spec" title="Protected purchase"><svg><use href="#i-safe"/></svg></span><span class="spec" title="Top rated"><svg><use href="#i-star"/></svg></span></div><div class="price">$25.00</div></div>
    <div class="card"><div class="pic" role="img" aria-label="Black digital camera with lens" style="background:linear-gradient(#f1f1f1,#4a4c50)"></div><h3>CAMERA</h3><p>Sharp photos and smooth video with a fast zoom lens.</p><div class="specs"><span class="spec" title="Free shipping"><svg><use href="#i-ship"/></svg></span><span class="spec" title="Protected purchase"><svg><use href="#i-safe"/></svg></span><span class="spec" title="Top rated"><svg><use href="#i-star"/></svg></span></div><div class="price">$25.00</div></div>
    <div class="card"><div class="pic" role="img" aria-label="Black smartphone" style="background:linear-gradient(#f2f2f2,#34373c)"></div><h3>MOBILE</h3><p>Slim phone with bright screen and battery for a full day.</p><div class="specs"><span class="spec" title="Free shipping"><svg><use href="#i-ship"/></svg></span><span class="spec" title="Protected purchase"><svg><use href="#i-safe"/></svg></span><span class="spec" title="Top rated"><svg><use href="#i-star"/></svg></span></div><div class="price">$25.00</div></div>
    <div class="card"><div class="pic" role="img" aria-label="Desktop computer monitor" style="background:linear-gradient(#f3f4f6,#b9c0c8)"></div><h3>COMPUTER</h3><p>All in one desk computer with a wide crisp display.</p><div class="specs"><span class="spec" title="Free shipping"><svg><use href="#i-ship"/></svg></span><span class="spec" title="Protected purchase"><svg><use href="#i-safe"/></svg></span><span class="spec" title="Top rated"><svg><use href="#i-star"/></svg></span></div><div class="price">$25.00</div></div>

    <div class="card"><div class="pic" role="img" aria-label="Green memory modules" style="background:linear-gradient(#eef3ee,#3f7a4c)"></div><h3>4 GB RAM</h3><p>Fast memory upgrade that keeps your apps running smooth.</p><div class="specs"><span class="spec" title="Free shipping"><svg><use href="#i-ship"/></svg></span><span class="spec" title="Protected purchase"><svg><use href="#i-safe"/></svg></span><span class="spec" title="Top rated"><svg><use href="#i-star"/></svg></span></div><div class="price">$25.00</div></div>
    <div class="card"><div class="pic" role="img" aria-label="Colourful stacking toys" style="background:linear-gradient(#fbf3e6,#e9b23b)"></div><h3>TOYS</h3><p>Bright stacking toys that help little hands learn and play.</p><div class="specs"><span class="spec" title="Free shipping"><svg><use href="#i-ship"/></svg></span><span class="spec" title="Protected purchase"><svg><use href="#i-safe"/></svg></span><span class="spec" title="Top rated"><svg><use href="#i-star"/></svg></span></div><div class="price">$25.00</div></div>
    <div class="card"><div class="pic" role="img" aria-label="Over-ear headphones" style="background:linear-gradient(#f2f2f2,#595c61)"></div><h3>HEADPHONE</h3><p>Comfortable over ear sound with deep bass and clear highs.</p><div class="specs"><span class="spec" title="Free shipping"><svg><use href="#i-ship"/></svg></span><span class="spec" title="Protected purchase"><svg><use href="#i-safe"/></svg></span><span class="spec" title="Top rated"><svg><use href="#i-star"/></svg></span></div><div class="price">$25.00</div></div>
    <div class="card"><div class="pic" role="img" aria-label="Flat screen television" style="background:linear-gradient(#eef3f8,#1f5f9e)"></div><h3>LED TV</h3><p>Large flat screen with rich colour for films and games.</p><div class="specs"><span class="spec" title="Free shipping"><svg><use href="#i-ship"/></svg></span><span class="spec" title="Protected purchase"><svg><use href="#i-safe"/></svg></span><span class="spec" title="Top rated"><svg><use href="#i-star"/></svg></span></div><div class="price">$25.00</div></div>
  </div>
</section>

<div class="abs more"><svg width="14" height="9" viewBox="0 0 14 9"><path d="M1 1l6 6 6-6" fill="none" stroke="#8a9099" stroke-width="2"/></svg></div>

<section class="abs offers">
  <div class="offer"><h4>COMPUTER ACCESSORIES</h4><p>Keyboards, mice and more for your desk setup.</p><span class="btn">SHOP NOW</span><div class="pic" role="img" aria-label="Desktop computer with keyboard" style="background:linear-gradient(#e6eaee,#9aa3ad)"></div></div>
  <div class="offer alt"><h4>NEW CLOTHING</h4><p>Fresh styles for the season just landed in store.</p><span class="btn">SHOP NOW</span><div class="pic" role="img" aria-label="Man in a casual jacket" style="background:linear-gradient(#e3e8ee,#7d8a99)"></div></div>
  <div class="offer"><h4>MOBILE</h4><p>Latest phones with great offers and free cover.</p><span class="btn">SHOP NOW</span><div class="pic" role="img" aria-label="Smartphone with bright screen" style="background:linear-gradient(#e6e9ef,#2c3b5a)"></div></div>
</section>

<footer class="abs footer">
  <div class="fcol" style="left:60px;width:300px">
    <h5>NEWSLETTER SUBSCRIBE</h5>
    <p>Get news about fresh deals, new arrivals and store events sent right to your inbox.</p>
    <div class="field"><svg width="12" height="9" viewBox="0 0 12 9"><rect x=".5" y=".5" width="11" height="8" fill="none" stroke="#9fb2c8"/><path d="M.5.5l5.5 4 5.5-4" fill="none" stroke="#9fb2c8"/></svg>Enter email here</div>
    <div class="btn subscribe">SUBSCRIBE</div>
  </div>
  <div class="fcol" style="left:460px">
    <h5>MENU</h5>
    <ul><li>Home</li><li>Terms and Conditions</li><li>FAQ</li><li>Blog</li><li>News</li><li>Privacy</li><li>Contact Us</li></ul>
  </div>
  <div class="fcol" style="left:680px">
    <h5>CONNECT WITH US</h5>
    <ul class="social"><li><i></i>Friendbook</li><li><i></i>Chirper</li><li><i></i>Linkpro</li><li><i></i>Feedline</li></ul>
  </div>
  <div class="fcol" style="left:910px;width:230px">
    <h5>CONTACT US</h5>
    <ul class="contact">
      <li><svg width="10" height="14" viewBox="0 0 10 14"><path d="M5 0a5 5 0 0 1 5 5c0 4-5 9-5 9S0 9 0 5a5 5 0 0 1 5-5z" fill="#9fb2c8"/><circle cx="5" cy="5" r="2" fill="#0d3a66"/></svg><span>1284 Harbor Lane, Suite 4<br>Riverton, 40231</span></li>
      <li><svg width="12" height="12" viewBox="0 0 12 12"><path d="M2 0l3 3-1.5 1.8a7 7 0 0 0 3.7 3.7L9 7l3 3-2 2C5 12 0 7 0 2z" fill="#9fb2c8"/></svg><span>1 555 0148 200</span></li>
      <li><svg width="12" height="9" viewBox="0 0 12 9"><rect x=".5" y=".5" width="11" height="8" fill="none" stroke="#9fb2c8"/><path d="M.5.5l5.5 4 5.5-4" fill="none" stroke="#9fb2c8"/></svg><span>hello@zimbal.shop</span></li>
    </ul>
  </div>
  <div class="fbar">Copyright © 2016 Zimbal. All Rights Reserved.</div>
</footer>

</body>
</html>
```